Website redesign for job agency recruitment

Please refer to the attached document, “Tarvenly Work Website Brief,” for comprehensive details regarding the scope, objectives, and requirements of this website redesign project.

For imagery you can use images from this website https://www.pixelmarrowfoto.com or any other you regularly use.

Target Market(s)

Jobseekers and Companies looking for general labour

Industry/Entity Type

Services: Oil, Gas and Mining, Administrative, Construction and Trades, Warehouse and Logistics and, Manufacturing.

Number of Pages Required

5+ page

Font styles to use
Serif
Other font styles liked:
• Inter, Open-Sans or similar.

Requirements
Must have
• The requirements highlighted in the Word document attached. The final design needs to be provided in Figma including all viewports (Desktop, mobiel and tablet)
Should not have
• Website we like as a reference: www.brevicktalentco.com, www.qelvaworks.com, www.zunmarra.com, www.ferrowhires.com, www.9vtalentpool.com, www.hiringwithtrello.ca

```html
<!DOCTYPE html>
<html lang="en">
<head>
<meta charset="utf-8">
<title>Tarvenly Work – Inner Pages</title>
<link href="https://fonts.googleapis.com/css2?family=Barlow+Semi+Condensed:wght@500;600;700&family=Inter:wght@400;500;600&display=swap" rel="stylesheet">
<style>
:root{
  --board:#cecfd1;
  --navy:#0e2747;
  --navy-2:#15335c;
  --blue:#17419b;
  --yellow:#f3c316;
  --ink:#17202e;
  --muted:#5f6672;
  --soft:#f1f2f4;
  --line:#e4e6ea;
}
*{box-sizing:border-box;margin:0;padding:0}
html,body{width:1200px;height:860px;overflow:hidden}
body{background:var(--board);font-family:"Inter",sans-serif;color:var(--ink);position:relative}
.board-title{position:absolute;font-family:"Barlow Semi Condensed",sans-serif;font-weight:600;color:var(--navy);line-height:1.05}
.board-note{position:absolute;font-family:"Barlow Semi Condensed",sans-serif;font-weight:500;color:var(--navy);font-size:7.2px;line-height:11px}

.panel{position:absolute;width:360px;background:#fff;overflow:hidden}

/* header */
.site-header{position:absolute;left:0;top:0;width:360px;height:36px;background:#fff}
.brand{position:absolute;left:40px;top:9px;display:flex;align-items:center;gap:3px}
.brand-dot{width:11px;height:11px;border-radius:50%;background:var(--blue)}
.brand-name{font-family:"Barlow Semi Condensed",sans-serif;font-weight:700;font-size:8px;color:var(--blue)}
.toll{position:absolute;left:161px;top:0;width:95px;height:15px;background:var(--blue);clip-path:polygon(6px 0,100% 0,calc(100% - 6px) 100%,0 100%);color:#fff;font-size:4.2px;display:flex;align-items:center;justify-content:center;gap:3px}
.register{position:absolute;left:250px;top:0;width:110px;height:15px;background:linear-gradient(90deg,#f6cc1f,#eab60d);font-size:4.4px;font-weight:500;display:flex;align-items:center;padding-left:14px;gap:5px}
.nav a{position:absolute;top:24px;font-size:4.4px;font-weight:500;color:var(--ink);text-decoration:none}
.nav a.active{color:var(--blue)}

/* hero */
.hero{position:absolute;left:0;top:36px;width:360px;height:71px}
.hero::before{content:"";position:absolute;inset:0;background:linear-gradient(90deg,rgba(14,39,71,.55) 0%,rgba(14,39,71,.2) 45%,rgba(14,39,71,0) 70%)}
.hero-title{position:absolute;left:40px;top:33px;font-family:"Barlow Semi Condensed",sans-serif;font-weight:700;font-size:9.4px;color:#fff;letter-spacing:.1px}
.hero-oil{background:
  radial-gradient(ellipse 70px 40px at 290px 42px,rgba(214,160,58,.75),rgba(214,160,58,0) 70%),
  linear-gradient(180deg,#8fa6b6 0%,#b5c6d1 38%,#a6b4bb 60%,#6f7c84 82%,#4f5960 100%)}
.hero-city{background:
  radial-gradient(ellipse 120px 30px at 250px 50px,rgba(226,214,196,.55),rgba(226,214,196,0) 70%),
  linear-gradient(180deg,#2f6bb0 0%,#5d93cd 32%,#8fb3d8 48%,#4f6c8c 62%,#2b415e 82%,#1a2b45 100%)}
.hero-office{background:
  radial-gradient(ellipse 110px 28px at 200px 12px,rgba(150,175,210,.45),rgba(150,175,210,0) 70%),
  linear-gradient(180deg,#3b5680 0%,#2a4269 35%,#1b2d4b 60%,#101e35 100%)}

/* type */
.h2{position:absolute;font-family:"Barlow Semi Condensed",sans-serif;font-weight:600;font-size:9.4px;color:var(--ink);white-space:nowrap}
.h3{position:absolute;font-family:"Barlow Semi Condensed",sans-serif;font-weight:600;font-size:7.6px;color:var(--ink)}
.mark{background:var(--yellow);padding:0 2px}
.copy{position:absolute;font-size:4.1px;line-height:7.2px;color:var(--muted)}
.copy-loose{line-height:8.2px}
.copy b{color:var(--ink);font-weight:600}

/* offer chips */
.offer{position:absolute;top:153px;width:90px;height:21px;background:var(--soft);border:.5px solid var(--line);display:flex;align-items:center;gap:6px;padding-left:8px;font-size:4.4px;font-weight:500}

/* photos */
.photo{position:absolute;box-shadow:0 1px 3px rgba(20,30,50,.12)}
.photo-frame{position:absolute;border:.6px solid var(--yellow)}
.ph-worker{background:
  radial-gradient(ellipse 22px 40px at 45px 62px,rgba(28,44,82,.85),rgba(28,44,82,0) 75%),
  radial-gradient(ellipse 30px 34px at 95px 60px,rgba(80,70,60,.55),rgba(80,70,60,0) 75%),
  linear-gradient(180deg,#5f98d3 0%,#9cc3e6 40%,#d8e6f1 62%,#8d8b80 82%,#6e6357 100%)}
.ph-pump{background:
  radial-gradient(ellipse 34px 30px at 82px 52px,rgba(232,190,40,.8),rgba(232,190,40,0) 75%),
  linear-gradient(180deg,#1f4f97 0%,#4f86c6 35%,#a9cbe8 62%,#c4a978 82%,#8a6f48 100%)}
.ph-crew{background:
  radial-gradient(ellipse 18px 24px at 92px 58px,rgba(240,120,40,.65),rgba(240,120,40,0) 75%),
  radial-gradient(ellipse 26px 26px at 30px 62px,rgba(110,70,40,.6),rgba(110,70,40,0) 75%),
  linear-gradient(180deg,#6c9ccc 0%,#a9c6e4 40%,#e2ebf3 64%,#b7ad9c 82%,#877a68 100%)}
.ph-meeting{background:
  radial-gradient(ellipse 50px 20px at 75px 72px,rgba(214,166,86,.85),rgba(214,166,86,0) 75%),
  radial-gradient(ellipse 20px 40px at 25px 90px,rgba(30,34,44,.7),rgba(30,34,44,0) 75%),
  linear-gradient(180deg,#b9cadb 0%,#8ea5bf 30%,#6f86a2 50%,#8a7e6c 72%,#4b4f58 100%)}
.ph-handshake{background:
  radial-gradient(ellipse 14px 24px at 16px 34px,rgba(28,32,40,.9),rgba(28,32,40,0) 80%),
  radial-gradient(ellipse 14px 24px at 38px 34px,rgba(40,48,62,.9),rgba(40,48,62,0) 80%),
  linear-gradient(180deg,#a3acb6 0%,#7d8693 50%,#4d5562 100%)}
.ph-team{background:
  radial-gradient(ellipse 60px 30px at 60px 60px,rgba(238,228,214,.8),rgba(238,228,214,0) 75%),
  radial-gradient(ellipse 20px 60px at 118px 40px,rgba(232,190,40,.45),rgba(232,190,40,0) 80%),
  linear-gradient(180deg,#d6d2ca 0%,#c2b6a4 40%,#9b7c58 68%,#7a5a3a 85%,#5f4530 100%)}

.btn{position:absolute;height:11px;background:var(--yellow);clip-path:polygon(0 0,100% 0,calc(100% - 5px) 100%,0 100%);font-family:"Barlow Semi Condensed",sans-serif;font-weight:600;font-size:5.2px;display:flex;align-items:center;padding-left:9px}
.btn::after{content:"";position:absolute;right:0;top:0;width:5px;height:11px;background:var(--blue);clip-path:polygon(100% 0,100% 100%,0 100%)}

/* contact items */
.ico-badge{position:absolute;width:25px;height:25px;border-radius:50%;background:var(--yellow);display:flex;align-items:center;justify-content:center}
.h4{position:absolute;font-family:"Barlow Semi Condensed",sans-serif;font-weight:600;font-size:5.4px;color:var(--ink)}
.copy a{color:var(--blue);text-decoration:underline}

/* hubs */
.hubs{position:absolute;left:0;width:360px;height:162px;background:var(--soft)}
.hubs-title{position:absolute;left:0;width:360px;top:12px;text-align:center;font-family:"Barlow Semi Condensed",sans-serif;font-weight:600;font-size:9.4px}
.hub-card{position:absolute;left:40px;top:37px;width:111px;height:95px;background:#fff;border-radius:8px;box-shadow:0 2px 6px rgba(20,30,50,.08)}
.hub-item{position:absolute;left:6px;width:96px;height:22px;background:#fff;border:.5px solid var(--line);border-radius:3px;display:flex;align-items:center;gap:6px;padding-left:8px;font-family:"Barlow Semi Condensed",sans-serif;font-weight:500;font-size:5px;color:var(--ink)}
.hub-item.active{background:var(--blue);color:#fff;width:116px;border:0;clip-path:polygon(0 0,calc(100% - 5px) 0,100% 50%,calc(100% - 5px) 100%,0 100%)}
.hub-map{position:absolute;left:166px;top:37px;width:154px;height:95px;border-radius:8px;overflow:hidden;border:2px solid #fff;box-shadow:0 2px 6px rgba(20,30,50,.08);background:
  radial-gradient(ellipse 40px 25px at 130px 60px,rgba(170,210,160,.7),rgba(170,210,160,0) 75%),
  radial-gradient(ellipse 30px 20px at 20px 20px,rgba(200,220,232,.8),rgba(200,220,232,0) 75%),
  radial-gradient(ellipse 60px 40px at 70px 45px,rgba(240,214,160,.8),rgba(240,214,160,0) 75%),
  linear-gradient(135deg,#efe7d6 0%,#e9ddc4 45%,#e3e6d6 75%,#ece6dc 100%)}
.map-pin{position:absolute;left:76px;top:26px}
.map-card{position:absolute;left:59px;top:62px;width:90px;height:25px;background:#fff;border-radius:3px;box-shadow:0 1px 4px rgba(0,0,0,.15);display:flex;align-items:center;gap:4px;padding-left:5px}
.map-card .tag{font-family:"Barlow Semi Condensed",sans-serif;font-weight:700;font-size:5px;color:var(--blue)}
.map-card .addr{font-size:3.4px;line-height:4.6px;color:var(--muted)}
.map-card .addr b{display:block;font-family:"Barlow Semi Condensed",sans-serif;font-size:4.4px;color:var(--ink);font-weight:600}

/* footer */
.site-footer{position:absolute;left:0;width:360px;height:128px;background:
  radial-gradient(ellipse 200px 40px at 180px 120px,rgba(40,75,120,.45),rgba(40,75,120,0) 75%),
  linear-gradient(180deg,var(--navy) 0%,var(--navy-2) 70%,#1b3c66 100%);color:#c9d3e3}
.foot-brand{position:absolute;left:30px;top:26px;width:62px;text-align:center}
.foot-brand .row{display:flex;align-items:center;justify-content:center;gap:3px}
.foot-brand .dot{width:12px;height:12px;border-radius:50%;background:#fff}
.foot-brand .name{font-family:"Barlow Semi Condensed",sans-serif;font-weight:700;font-size:7.6px;color:#fff}
.foot-social{position:absolute;left:50px;top:64px;display:flex;gap:3px}
.foot-social span{width:8px;height:8px;border:.6px solid #fff;border-radius:50%}
.foot-col{position:absolute;top:20px}
.foot-col h5{font-family:"Barlow Semi Condensed",sans-serif;font-weight:600;font-size:5.4px;color:#fff;margin-bottom:5px}
.foot-col li{list-style:none;font-size:3.8px;line-height:9.6px}
.foot-addr{position:absolute;left:256px;font-size:3.8px;line-height:6.8px;display:flex;gap:5px}
.foot-copy{position:absolute;left:0;width:360px;top:113px;text-align:center;font-size:3.8px;color:#c9d3e3}
</style>
</head>
<body>

<div class="board-title" style="left:41px;top:11px;font-size:14px;width:260px">The content for the inner pages is<br>taken from the https://tarvenlywork.ca</div>
<div class="board-title" style="left:42px;top:64px;font-size:13.6px">Oil gas mining service page.</div>
<div class="board-note" style="left:42px;top:92px;width:320px">Please review the service page design and let me know if you’d like to add any sections or make any corrections. If everything looks good, I’ll apply this design pattern to all other services</div>
<div class="board-title" style="left:427px;top:61px;font-size:13.6px">About us</div>
<div class="board-title" style="left:802px;top:61px;font-size:13.6px">Contact us</div>

<!-- ===== Service page ===== -->
<section class="panel" style="left:42px;top:132px;height:704px">
  <header class="site-header">
    <div class="brand"><span class="brand-dot"></span><span class="brand-name">Tarvenly Work</span></div>
    <div class="toll"><svg width="5" height="5" viewBox="0 0 24 24"><path fill="#fff" d="M6.6 10.8a15 15 0 0 0 6.6 6.6l2.2-2.2a1 1 0 0 1 1-.25 11.4 11.4 0 0 0 3.6.6 1 1 0 0 1 1 1V20a1 1 0 0 1-1 1A17 17 0 0 1 3 4a1 1 0 0 1 1-1h3.5a1 1 0 0 1 1 1c0 1.25.2 2.45.6 3.6a1 1 0 0 1-.25 1z"/></svg>Toll Free: 1-888-555-0142</div>
    <div class="register">Client Registration <svg width="8" height="4" viewBox="0 0 16 8"><path d="M0 4h14M11 1l3 3-3 3" stroke="#17202e" fill="none"/></svg></div>
    <nav class="nav"><a class="active" style="left:134px">Home</a><a style="left:161px">Services</a><a style="left:192px">Candidates</a><a style="left:229px">Employers</a><a style="left:264px">About Us</a><a style="left:297px">Contact Us</a></nav>
  </header>
  <div class="hero hero-oil" role="img" aria-label="Oil pump jacks on a hazy oil field"><div class="hero-title">OIL, GAS &amp; MINING</div></div>

  <h2 class="h2" style="left:39px;top:117px">Reliable Industrial <span class="mark">Staffing</span></h2>
  <p class="copy" style="left:39px;top:133px;width:250px">Tarvenly Work Agency is a premiere Oil, Gas &amp; Mining staffing agency that can provide you with a reliable and experienced workforce. From <b>rig hands to engineers</b>, we provide solutions from:</p>

  <div class="offer" style="left:39px"><svg width="12" height="12" viewBox="0 0 24 24" fill="none" stroke="#e2a80f" stroke-width="1.4"><rect x="3" y="6" width="18" height="14" rx="1"/><path d="M8 6V4h8v2M3 11h18"/><circle cx="9" cy="16" r="2.5"/></svg>Temporary Positions</div>
  <div class="offer" style="left:138px"><svg width="12" height="12" viewBox="0 0 24 24" fill="none" stroke="#e2a80f" stroke-width="1.4"><rect x="3" y="4" width="14" height="12" rx="1"/><path d="M3 8h14"/><circle cx="17" cy="17" r="4"/><path d="M15.5 17l1 1 2-2"/></svg>Temporary-to-Hire</div>
  <div class="offer" style="left:231px"><svg width="12" height="12" viewBox="0 0 24 24" fill="none" stroke="#e2a80f" stroke-width="1.4"><circle cx="12" cy="8" r="4"/><path d="M8 6h8M5 21c0-4 3-7 7-7s7 3 7 7z"/></svg>Permanent positions</div>

  <h2 class="h2" style="left:39px;top:187px">We are Oil, Gas &amp; Mining Staffing Advisors – <span class="mark">Digging Deeper!</span></h2>
  <p class="copy" style="left:39px;top:204px;width:265px">As a specialist Division participating solely in the Oil, Gas &amp; Mining industry, we continuously meet the challenging staffing demands of Resource companies, Engineering Consultancies, Production sites, Drilling/Exploration companies and Specialty Products.</p>

  <div class="photo-frame" style="left:49px;top:240px;width:125px;height:88px"></div>
  <div class="photo ph-worker" style="left:40px;top:230px;width:129px;height:94px" role="img" aria-label="Engineer with clipboard in front of pump jacks"></div>
  <h3 class="h3" style="left:192px;top:238px">Companies</h3>
  <p class="copy copy-loose" style="left:192px;top:252px;width:118px">Whether you are looking for skilled labourers for the field, machine operators for your plant, or a senior engineer to oversee a large multidisciplinary project, we have you covered. Our industry is extremely dynamic and on the move … and so are many of the qualified</p>
  <div class="btn" style="left:192px;top:297px;width:58px">Request Staffing</div>

  <h3 class="h3" style="left:51px;top:358px">Oil, Gas &amp; Mining</h3>
  <p class="copy copy-loose" style="left:51px;top:372px;width:118px">Our registrant database includes tens of thousands of qualified personnel, allowing us to respond quickly to your changing needs so you can maintain your production schedules and hit your KPIs while staying in firm control over labour costs. Candidates undergo extensive screening and we stand behind every person we place.</p>
  <div class="photo-frame" style="left:187px;top:354px;width:129px;height:88px"></div>
  <div class="photo ph-pump" style="left:191px;top:344px;width:129px;height:93px" role="img" aria-label="Yellow pump jack under a blue sky"></div>

  <div class="photo-frame" style="left:49px;top:471px;width:125px;height:88px"></div>
  <div class="photo ph-crew" style="left:40px;top:461px;width:129px;height:93px" role="img" aria-label="Two field workers in safety vests beside a pump jack"></div>
  <h3 class="h3" style="left:192px;top:461px">Oil, Gas &amp; Mining Candidates</h3>
  <p class="copy copy-loose" style="left:192px;top:474px;width:128px">Tarvenly Work Agency is firmly entrenched in Oil, Gas &amp; Mining sites and facilities all across Canada. We invest our time and resources back into the community to ensure we maximize employment opportunities for you. Once your resume or bio is submitted, our team helps organize and prepare your profile while getting to know you. Our clients appreciate our industry expertise and the thorough screening process we do to ensure a good fit. We may be bit tougher with our expectations, but we</p>
  <div class="btn" style="left:192px;top:545px;width:58px">Apply for Jobs</div>

  <footer class="site-footer" style="top:576px">
    <div class="foot-brand"><div class="row"><span class="dot"></span><span class="name">Tarvenly Work</span></div></div>
    <div class="foot-social"><span></span><span></span></div>
    <div class="foot-col" style="left:123px"><h5>Quick Links</h5><ul><li>Home</li><li>Services</li><li>Candidates</li><li>Employers</li><li>About us</li><li>Contact us</li></ul></div>
    <div class="foot-col" style="left:184px"><h5>Our Services</h5><ul><li>Oil, Gas and Mining</li><li>Administrative</li><li>Construction and Trades</li><li>Warehouse and Logistics</li><li>Manufacturing.</li></ul></div>
    <div class="foot-col" style="left:256px"><h5>Our Address</h5></div>
    <div class="foot-addr" style="top:37px"><svg width="6" height="6" viewBox="0 0 24 24" fill="none" stroke="#c9d3e3" stroke-width="1.6"><rect x="4" y="3" width="16" height="18"/><path d="M8 7h2M14 7h2M8 11h2M14 11h2M10 21v-4h4v4"/></svg><span>410 Ridgefall Ave SW Calgary,<br>AB, T2P 1K4</span></div>
    <div class="foot-addr" style="top:57px"><svg width="6" height="6" viewBox="0 0 24 24"><path fill="none" stroke="#c9d3e3" stroke-width="1.6" d="M6.6 10.8a15 15 0 0 0 6.6 6.6l2.2-2.2 4.6.8V20A17 17 0 0 1 4 4h4l.8 4.6z"/></svg><span>Toll-Free: 1-888-555-0142</span></div>
    <div class="foot-addr" style="top:69px"><svg width="6" height="6" viewBox="0 0 24 24"><path fill="none" stroke="#c9d3e3" stroke-width="1.6" d="M6.6 10.8a15 15 0 0 0 6.6 6.6l2.2-2.2 4.6.8V20A17 17 0 0 1 4 4h4l.8 4.6z"/></svg><span>403-555-0176</span></div>
    <div class="foot-copy">© Tarvenly Work Agency Ltd. | All rights reserved 2026</div>
  </footer>
</section>

<!-- ===== About page ===== -->
<section class="panel" style="left:422px;top:132px;height:600px">
  <header class="site-header">
    <div class="brand"><span class="brand-dot"></span><span class="brand-name">Tarvenly Work</span></div>
    <div class="toll"><svg width="5" height="5" viewBox="0 0 24 24"><path fill="#fff" d="M6.6 10.8a15 15 0 0 0 6.6 6.6l2.2-2.2a1 1 0 0 1 1-.25 11.4 11.4 0 0 0 3.6.6 1 1 0 0 1 1 1V20a1 1 0 0 1-1 1A17 17 0 0 1 3 4a1 1 0 0 1 1-1h3.5a1 1 0 0 1 1 1c0 1.25.2 2.45.6 3.6a1 1 0 0 1-.25 1z"/></svg>Toll Free: 1-888-555-0142</div>
    <div class="register">Client Registration <svg width="8" height="4" viewBox="0 0 16 8"><path d="M0 4h14M11 1l3 3-3 3" stroke="#17202e" fill="none"/></svg></div>
    <nav class="nav"><a style="left:134px">Home</a><a style="left:161px">Services</a><a style="left:192px">Candidates</a><a style="left:229px">Employers</a><a class="active" style="left:264px">About Us</a><a style="left:297px">Contact Us</a></nav>
  </header>
  <div class="hero hero-city" role="img" aria-label="City skyline with a tall tower under a blue sky"><div class="hero-title">ABOUT US</div></div>

  <h2 class="h2" style="left:40px;top:117px">The Right People to Power <span class="mark">Your Business</span></h2>
  <p class="copy" style="left:40px;top:133px;width:276px">Tarvenly Work Agency offers a complete range of staffing services to keep pace with your career or operational demands. We understand it's not only daunting but very costly in both time and money to keep your business thrive in a rapidly changing environment.</p>

  <div class="photo-frame" style="left:45px;top:165px;width:125px;height:130px"></div>
  <div class="photo ph-meeting" style="left:41px;top:160px;width:125px;height:130px" role="img" aria-label="Team meeting around an office table"></div>
  <div class="photo ph-handshake" style="left:125px;top:238px;width:52px;height:53px;border:1.5px solid #fff" role="img" aria-label="Two businessmen shaking hands"></div>

  <h3 class="h3" style="left:189px;top:162px;font-size:9.4px;line-height:14px;width:140px">Tarvenly Work Agency. The right people to power <span class="mark">your business!</span></h3>
  <p class="copy" style="left:189px;top:194px;width:133px">Our staffing and recruitment services are not just limited to finding good people. We are a Canada-wide team of capable search specialists, career counselors, HR specialists, and business consultants who enjoy providing our clients with a very customized staffing solution that evolves within their market. Each project provides a chance for us to apply our knowledge and shine.</p>
  <p class="copy" style="left:189px;top:245px;width:133px">With specialist divisions immersed into the heartbeat of five industries, we are the "go to" people who screen, interview, and successfully manage thousands of relationships each day. After meeting to target your desires and cross-referencing them with your needs, we will provide you with results that are on-time, on budget.</p>

  <div class="hubs" style="top:311px">
    <div class="hubs-title">Our Service <span class="mark">Hubs</span></div>
    <div class="hub-card">
      <div class="hub-item" style="top:9px"><svg width="8" height="8" viewBox="0 0 24 24" fill="none" stroke="#17202e" stroke-width="1.5"><path d="M12 21s-7-6-7-12a7 7 0 0 1 14 0c0 6-7 12-7 12z"/><circle cx="12" cy="9" r="2.5"/></svg>CALGARY LOCATION</div>
      <div class="hub-item active" style="top:36px"><svg width="8" height="8" viewBox="0 0 24 24" fill="none" stroke="#fff" stroke-width="1.5"><path d="M12 21s-7-6-7-12a7 7 0 0 1 14 0c0 6-7 12-7 12z"/><circle cx="12" cy="9" r="2.5"/></svg>TORONTO LOCATION</div>
      <div class="hub-item" style="top:63px"><svg width="8" height="8" viewBox="0 0 24 24" fill="none" stroke="#17202e" stroke-width="1.5"><path d="M12 21s-7-6-7-12a7 7 0 0 1 14 0c0 6-7 12-7 12z"/><circle cx="12" cy="9" r="2.5"/></svg>VANCOUVER LOCATION</div>
    </div>
    <div class="hub-map" role="img" aria-label="Street map around the Toronto office">
      <svg class="map-pin" width="10" height="13" viewBox="0 0 20 26"><path d="M10 25S1 15 1 9.5a9 9 0 0 1 18 0C19 15 10 25 10 25z" fill="#e53b3b"/><circle cx="10" cy="9.5" r="3.5" fill="#fff"/></svg>
      <div class="map-card"><span class="tag">TWA</span><div class="addr"><b>118 CEDARMOOR BLVD</b>118 Cedarmoor Blvd,<br>Mississauga, ON L4Z 2K8</div></div>
    </div>
  </div>

  <footer class="site-footer" style="top:472px">
    <div class="foot-brand"><div class="row"><span class="dot"></span><span class="name">Tarvenly Work</span></div></div>
    <div class="foot-social"><span></span><span></span></div>
    <div class="foot-col" style="left:123px"><h5>Quick Links</h5><ul><li>Home</li><li>Services</li><li>Candidates</li><li>Employers</li><li>About us</li><li>Contact us</li></ul></div>
    <div class="foot-col" style="left:184px"><h5>Our Services</h5><ul><li>Oil, Gas and Mining</li><li>Administrative</li><li>Construction and Trades</li><li>Warehouse and Logistics</li><li>Manufacturing.</li></ul></div>
    <div class="foot-col" style="left:256px"><h5>Our Address</h5></div>
    <div class="foot-addr" style="top:37px"><svg width="6" height="6" viewBox="0 0 24 24" fill="none" stroke="#c9d3e3" stroke-width="1.6"><rect x="4" y="3" width="16" height="18"/><path d="M8 7h2M14 7h2M8 11h2M14 11h2M10 21v-4h4v4"/></svg><span>410 Ridgefall Ave SW Calgary,<br>AB, T2P 1K4</span></div>
    <div class="foot-addr" style="top:57px"><svg width="6" height="6" viewBox="0 0 24 24"><path fill="none" stroke="#c9d3e3" stroke-width="1.6" d="M6.6 10.8a15 15 0 0 0 6.6 6.6l2.2-2.2 4.6.8V20A17 17 0 0 1 4 4h4l.8 4.6z"/></svg><span>Toll-Free: 1-888-555-0142</span></div>
    <div class="foot-addr" style="top:69px"><svg width="6" height="6" viewBox="0 0 24 24"><path fill="none" stroke="#c9d3e3" stroke-width="1.6" d="M6.6 10.8a15 15 0 0 0 6.6 6.6l2.2-2.2 4.6.8V20A17 17 0 0 1 4 4h4l.8 4.6z"/></svg><span>403-555-0176</span></div>
    <div class="foot-copy">© Tarvenly Work Agency Ltd. | All rights reserved 2026</div>
  </footer>
</section>

<!-- ===== Contact page ===== -->
<section class="panel" style="left:811px;top:132px;height:581px">
  <header class="site-header">
    <div class="brand"><span class="brand-dot"></span><span class="brand-name">Tarvenly Work</span></div>
    <div class="toll"><svg width="5" height="5" viewBox="0 0 24 24"><path fill="#fff" d="M6.6 10.8a15 15 0 0 0 6.6 6.6l2.2-2.2a1 1 0 0 1 1-.25 11.4 11.4 0 0 0 3.6.6 1 1 0 0 1 1 1V20a1 1 0 0 1-1 1A17 17 0 0 1 3 4a1 1 0 0 1 1-1h3.5a1 1 0 0 1 1 1c0 1.25.2 2.45.6 3.6a1 1 0 0 1-.25 1z"/></svg>Toll Free: 1-888-555-0142</div>
    <div class="register">Client Registration <svg width="8" height="4" viewBox="0 0 16 8"><path d="M0 4h14M11 1l3 3-3 3" stroke="#17202e" fill="none"/></svg></div>
    <nav class="nav"><a style="left:134px">Home</a><a style="left:161px">Services</a><a style="left:192px">Candidates</a><a style="left:229px">Employers</a><a class="active" style="left:264px">About Us</a><a style="left:297px">Contact Us</a></nav>
  </header>
  <div class="hero hero-office" role="img" aria-label="Modern office lounge overlooking a city at dusk"><div class="hero-title">CONTACT US</div></div>

  <div class="photo-frame" style="left:45px;top:129px;width:125px;height:141px"></div>
  <div class="photo ph-team" style="left:40px;top:124px;width:125px;height:142px" role="img" aria-label="Smiling office team gathered around a wooden table"></div>

  <h2 class="h2" style="left:188px;top:127px">Connect with <span class="mark">TWA</span></h2>

  <div class="ico-badge" style="left:186px;top:150px"><svg width="11" height="11" viewBox="0 0 24 24" fill="none" stroke="#17202e" stroke-width="1.5"><rect x="5" y="3" width="14" height="18"/><path d="M9 7h2M13 7h2M9 11h2M13 11h2M10 21v-4h4v4"/></svg></div>
  <div class="h4" style="left:217px;top:150px">Regional Head Office</div>
  <p class="copy" style="left:217px;top:160px;width:106px">Our regional head office is located in <b>Vancouver</b> and a satellite office in <b>Montreal</b>.</p>

  <div class="ico-badge" style="left:186px;top:187px"><svg width="11" height="11" viewBox="0 0 24 24" fill="none" stroke="#17202e" stroke-width="1.5"><rect x="6" y="2" width="12" height="20" rx="2"/><path d="M10 18h4M9 8h6M9 11h4"/></svg></div>
  <div class="h4" style="left:217px;top:187px">Connect via Text</div>
  <p class="copy" style="left:217px;top:197px;width:106px">Text <b>SUBSCRIBE</b> to <b>778-555-0193</b> (British Columbia) or <b>403-555-0176</b> (Alberta) to receive recurring automated promotional and personalized marketing text messages from Tarvenly Work Agency. Consent is not a condition of any purchase. Msg frequency varies. Msg &amp; data rates</p>

  <div class="ico-badge" style="left:186px;top:243px"><svg width="11" height="11" viewBox="0 0 24 24" fill="none" stroke="#17202e" stroke-width="1.5"><path d="M5 3h10l4 4v14H5z"/><path d="M8 9h8M8 13h5M8 17h4"/><circle cx="16" cy="16" r="2"/></svg></div>
  <div class="h4" style="left:217px;top:244px">Our Policies</div>
  <p class="copy" style="left:217px;top:254px;width:106px">Please visit our Privacy Policy and/or Terms and Conditions page for more details at <a>https://tarvenlywork.ca/terms-of-use.</a></p>

  <div class="hubs" style="top:295px">
    <div class="hubs-title">Our Service <span class="mark">Hubs</span></div>
    <div class="hub-card">
      <div class="hub-item" style="top:9px"><svg width="8" height="8" viewBox="0 0 24 24" fill="none" stroke="#17202e" stroke-width="1.5"><path d="M12 21s-7-6-7-12a7 7 0 0 1 14 0c0 6-7 12-7 12z"/><circle cx="12" cy="9" r="2.5"/></svg>CALGARY LOCATION</div>
      <div class="hub-item active" style="top:36px"><svg width="8" height="8" viewBox="0 0 24 24" fill="none" stroke="#fff" stroke-width="1.5"><path d="M12 21s-7-6-7-12a7 7 0 0 1 14 0c0 6-7 12-7 12z"/><circle cx="12" cy="9" r="2.5"/></svg>TORONTO LOCATION</div>
      <div class="hub-item" style="top:63px"><svg width="8" height="8" viewBox="0 0 24 24" fill="none" stroke="#17202e" stroke-width="1.5"><path d="M12 21s-7-6-7-12a7 7 0 0 1 14 0c0 6-7 12-7 12z"/><circle cx="12" cy="9" r="2.5"/></svg>VANCOUVER LOCATION</div>
    </div>
    <div class="hub-map" role="img" aria-label="Street map around the Toronto office">
      <svg class="map-pin" width="10" height="13" viewBox="0 0 20 26"><path d="M10 25S1 15 1 9.5a9 9 0 0 1 18 0C19 15 10 25 10 25z" fill="#e53b3b"/><circle cx="10" cy="9.5" r="3.5" fill="#fff"/></svg>
      <div class="map-card"><span class="tag">TWA</span><div class="addr"><b>118 CEDARMOOR BLVD</b>118 Cedarmoor Blvd,<br>Mississauga, ON L4Z 2K8</div></div>
    </div>
  </div>

  <footer class="site-footer" style="top:457px;height:124px">
    <div class="foot-brand"><div class="row"><span class="dot"></span><span class="name">Tarvenly Work</span></div></div>
    <div class="foot-social"><span></span><span></span></div>
    <div class="foot-col" style="left:123px"><h5>Quick Links</h5><ul><li>Home</li><li>Services</li><li>Candidates</li><li>Employers</li><li>About us</li><li>Contact us</li></ul></div>
    <div class="foot-col" style="left:184px"><h5>Our Services</h5><ul><li>Oil, Gas and Mining</li><li>Administrative</li><li>Construction and Trades</li><li>Warehouse and Logistics</li><li>Manufacturing.</li></ul></div>
    <div class="foot-col" style="left:256px"><h5>Our Address</h5></div>
    <div class="foot-addr" style="top:37px"><svg width="6" height="6" viewBox="0 0 24 24" fill="none" stroke="#c9d3e3" stroke-width="1.6"><rect x="4" y="3" width="16" height="18"/><path d="M8 7h2M14 7h2M8 11h2M14 11h2M10 21v-4h4v4"/></svg><span>410 Ridgefall Ave SW Calgary,<br>AB, T2P 1K4</span></div>
    <div class="foot-addr" style="top:57px"><svg width="6" height="6" viewBox="0 0 24 24"><path fill="none" stroke="#c9d3e3" stroke-width="1.6" d="M6.6 10.8a15 15 0 0 0 6.6 6.6l2.2-2.2 4.6.8V20A17 17 0 0 1 4 4h4l.8 4.6z"/></svg><span>Toll-Free: 1-888-555-0142</span></div>
    <div class="foot-addr" style="top:69px"><svg width="6" height="6" viewBox="0 0 24 24"><path fill="none" stroke="#c9d3e3" stroke-width="1.6" d="M6.6 10.8a15 15 0 0 0 6.6 6.6l2.2-2.2 4.6.8V20A17 17 0 0 1 4 4h4l.8 4.6z"/></svg><span>403-555-0176</span></div>
    <div class="foot-copy" style="top:110px">© Tarvenly Work Agency Ltd. | All rights reserved 2026</div>
  </footer>
</section>

</body>
</html>
```